Musical download and streaming website

hello designers, I want to start up a musical website where users can download and rate music of different genres such as RnB, Hip hop, rock, afro-pop. This website should be attractive and contemporary. There will be a search column for different songs. Music files will be mp3, mwa, and others. I like blue, gold, pink and indigo colors. My website should resemble http://tunovalt.com. There should be good imaginary of music stars on my website.

```html
<!DOCTYPE html>
<html lang="en">
<head>
<meta charset="utf-8">
<title>Velora Music</title>
<link href="https://fonts.googleapis.com/css2?family=Lobster&family=Open+Sans:wght@400;600;700&display=swap" rel="stylesheet">
<style>
:root{
  --indigo:#2e2a8a;
  --pink:#ff3f7f;
  --gold:#f5b82e;
  --paper:#f7f7f7;
  --text:#222;
  --footer:#000;
}
*{margin:0;padding:0;box-sizing:border-box}
html,body{width:1125px;height:1200px;overflow:hidden;background:#fff;font-family:'Open Sans',Arial,sans-serif;color:var(--text)}
.page{position:relative;width:1125px;height:1200px}

.masthead{position:absolute;left:0;top:0;width:1125px;height:270px;
  background:radial-gradient(circle at 560px 40px,#fbeff3 0,#f3f0f4 160px,#ececec 420px,#e6e6e6 100%)}
.masthead-art{position:absolute;left:765px;top:0;width:240px;height:225px;border-radius:50%;
  background:radial-gradient(circle at 50% 45%,rgba(233,94,150,.55),rgba(138,200,80,.25) 55%,rgba(236,236,236,0) 72%)}
.brand{position:absolute;left:0;width:1125px;top:48px;text-align:center;font-weight:700;font-size:40px;color:var(--indigo);letter-spacing:-.5px}
.brand .dot{display:inline-block;width:14px;height:14px;border-radius:50%;background:var(--gold);margin-left:8px;vertical-align:middle}

.search{position:absolute;left:375px;top:165px;width:375px;height:31px;display:flex}
.search-field{flex:1;border:1px solid #bdbdbd;border-right:none;background:#fff;display:flex;align-items:center;padding-left:8px;font-size:12px;color:#777}
.search-field svg{margin-right:6px}
.search-button{width:98px;background:var(--indigo);color:#fff;font-size:12px;display:flex;align-items:center;justify-content:center;letter-spacing:.3px}

.genres{position:absolute;left:0;width:1125px;top:239px;display:flex;justify-content:center;gap:21px;font-size:12.5px;color:#444}
.genres li{list-style:none;display:flex;align-items:center}
.genres li::before{content:"";width:7px;height:7px;border-radius:50%;background:#aaa;margin-right:7px}
.genres li.is-active::before{background:var(--pink)}

.artist-bar{position:absolute;left:0;top:270px;width:1125px;height:34px;background:var(--pink);color:#fff;
  display:flex;align-items:center;padding-left:158px;font-size:10.5px;font-weight:700;white-space:nowrap}
.artist-bar .label{font-size:12px;margin-right:12px;letter-spacing:.3px}
.artist-bar .letters{display:flex;gap:6.4px}
.artist-bar .letters .is-active{color:var(--gold)}
.artist-bar .digits{display:flex;gap:6.3px;margin-left:16px}
.artist-bar .tops{margin-left:10px;display:flex;gap:8px}

.hero{position:absolute;left:0;top:304px;width:1125px;height:281px;
  background:linear-gradient(90deg,#2e2a26 0%,#4a3f36 30%,#8b7261 52%,#c9a998 68%,#6f5a4c 85%,#3b302a 100%)}
.hero-title{position:absolute;left:177px;top:78px;font-family:'Lobster',cursive;font-size:42px;color:#fff}

.charts{position:absolute;left:124px;top:563px;width:877px;height:359px;background:var(--paper);
  box-shadow:0 0 4px rgba(0,0,0,.25)}
.chart-title{position:absolute;top:26px;font-family:'Lobster',cursive;font-size:23px;font-weight:400;color:var(--indigo)}
.chart-rule{position:absolute;top:60px;height:1px;background:#c8c8c8;width:373px}
.chart-list{position:absolute;top:93px;list-style:none;font-size:11.2px;color:#333}
.chart-list li{height:22.45px;display:flex;align-items:center;white-space:nowrap}
.chart-list svg{margin-right:9px;flex:none}
.more{position:absolute;left:767px;top:333px;font-size:11.5px;color:var(--pink);display:flex;align-items:center;gap:8px}

.about{position:absolute;left:145px;top:940px;width:845px}
.about-lead{font-size:13.2px;color:var(--indigo);margin-bottom:12px}
.about p.body{font-size:9.6px;line-height:18px;color:#111;margin-bottom:18px}

.footer{position:absolute;left:0;top:1130px;width:1125px;height:70px;background:var(--footer);color:#fff;text-align:center}
.footer-links{margin-top:18px;font-size:10.2px}
.footer-links span.sep{margin:0 6px}
.footer-copy{margin-top:9px;font-size:8.5px}
</style>
</head>
<body>
<div class="page">

  <header class="masthead">
    <div class="masthead-art" role="img" aria-label="Colourful cluster of musical notes and a treble clef"></div>
    <div class="brand">Velora Music<span class="dot"></span></div>

    <div class="search">
      <div class="search-field">
        <svg width="11" height="11" viewBox="0 0 12 12"><circle cx="5" cy="5" r="3.6" fill="none" stroke="#555" stroke-width="1.6"/><line x1="7.6" y1="7.6" x2="11" y2="11" stroke="#555" stroke-width="1.8"/></svg>
        Search
      </div>
      <div class="search-button">SEARCH</div>
    </div>

    <ul class="genres">
      <li class="is-active">RNB</li>
      <li>HIP HOP</li>
      <li>ROCK</li>
      <li>AFRO-POP</li>
    </ul>
  </header>

  <nav class="artist-bar">
    <span class="label">ARTIST LIST :</span>
    <span class="letters"><span class="is-active">A</span><span>B</span><span>C</span><span>D</span><span>E</span><span>F</span><span>G</span><span>H</span><span>I</span><span>J</span><span>K</span><span>L</span><span>M</span><span>N</span><span>O</span><span>P</span><span>Q</span><span>R</span><span>S</span><span>T</span><span>U</span><span>V</span><span>W</span><span>X</span><span>Y</span><span>Z</span></span>
    <span class="digits"><span>0</span><span>1</span><span>2</span><span>3</span><span>4</span><span>5</span><span>6</span><span>7</span><span>8</span><span>9</span></span>
    <span class="tops"><span>TOP 100 SONGS</span><span>TOP 100 ARTISTS</span></span>
  </nav>

  <section class="hero" role="img" aria-label="Photo of a young woman with headphones dancing joyfully">
    <div class="hero-title">Velora Music</div>
  </section>

  <section class="charts">
    <svg width="0" height="0" style="position:absolute">
      <defs>
        <symbol id="note" viewBox="0 0 12 12"><path d="M4 2 L11 0.5 V8.5 A1.8 1.5 0 1 1 9.6 7 V3 L5.4 3.9 V10 A1.8 1.5 0 1 1 4 8.5 Z" fill="#222"/></symbol>
      </defs>
    </svg>

    <h2 class="chart-title" style="left:29px">Top 20 artists</h2>
    <div class="chart-rule" style="left:29px"></div>
    <h2 class="chart-title" style="left:464px">Top 20 Songs</h2>
    <div class="chart-rule" style="left:464px"></div>

    <ul class="chart-list" style="left:29px">
      <li><svg width="10" height="10"><use href="#note"/></svg>Copper Finch</li>
      <li><svg width="10" height="10"><use href="#note"/></svg>Odalys Renn</li>
      <li><svg width="10" height="10"><use href="#note"/></svg>Theo Marchwood</li>
      <li><svg width="10" height="10"><use href="#note"/></svg>Ivo Kestrel</li>
      <li><svg width="10" height="10"><use href="#note"/></svg>Sable Harbor</li>
      <li><svg width="10" height="10"><use href="#note"/></svg>The Lantern Pines</li>
      <li><svg width="10" height="10"><use href="#note"/></svg>Priya Castellan</li>
      <li><svg width="10" height="10"><use href="#note"/></svg>Wren Okafor</li>
      <li><svg width="10" height="10"><use href="#note"/></svg>Dario Flint</li>
      <li><svg width="10" height="10"><use href="#note"/></svg>Www.melodybin.pk</li>
    </ul>
    <ul class="chart-list" style="left:233px">
      <li><svg width="10" height="10"><use href="#note"/></svg>Copper Finch</li>
      <li><svg width="10" height="10"><use href="#note"/></svg>Odalys Renn</li>
      <li><svg width="10" height="10"><use href="#note"/></svg>Theo Marchwood</li>
      <li><svg width="10" height="10"><use href="#note"/></svg>Ivo Kestrel</li>
      <li><svg width="10" height="10"><use href="#note"/></svg>Sable Harbor</li>
      <li><svg width="10" height="10"><use href="#note"/></svg>The Lantern Pines</li>
      <li><svg width="10" height="10"><use href="#note"/></svg>Priya Castellan</li>
      <li><svg width="10" height="10"><use href="#note"/></svg>Wren Okafor</li>
      <li><svg width="10" height="10"><use href="#note"/></svg>Dario Flint</li>
      <li><svg width="10" height="10"><use href="#note"/></svg>Www.melodybin.pk</li>
    </ul>
    <ul class="chart-list" style="left:465px">
      <li><svg width="10" height="10"><use href="#note"/></svg>Copper Finch</li>
      <li><svg width="10" height="10"><use href="#note"/></svg>Odalys Renn</li>
      <li><svg width="10" height="10"><use href="#note"/></svg>Theo Marchwood</li>
      <li><svg width="10" height="10"><use href="#note"/></svg>Ivo Kestrel</li>
      <li><svg width="10" height="10"><use href="#note"/></svg>Sable Harbor</li>
      <li><svg width="10" height="10"><use href="#note"/></svg>The Lantern Pines</li>
      <li><svg width="10" height="10"><use href="#note"/></svg>Priya Castellan</li>
      <li><svg width="10" height="10"><use href="#note"/></svg>Wren Okafor</li>
      <li><svg width="10" height="10"><use href="#note"/></svg>Dario Flint</li>
      <li><svg width="10" height="10"><use href="#note"/></svg>Www.melodybin.pk</li>
    </ul>
    <ul class="chart-list" style="left:698px">
      <li><svg width="10" height="10"><use href="#note"/></svg>Copper Finch</li>
      <li><svg width="10" height="10"><use href="#note"/></svg>Odalys Renn</li>
      <li><svg width="10" height="10"><use href="#note"/></svg>Theo Marchwood</li>
      <li><svg width="10" height="10"><use href="#note"/></svg>Ivo Kestrel</li>
      <li><svg width="10" height="10"><use href="#note"/></svg>Sable Harbor</li>
      <li><svg width="10" height="10"><use href="#note"/></svg>The Lantern Pines</li>
      <li><svg width="10" height="10"><use href="#note"/></svg>Priya Castellan</li>
      <li><svg width="10" height="10"><use href="#note"/></svg>Wren Okafor</li>
      <li><svg width="10" height="10"><use href="#note"/></svg>Dario Flint</li>
      <li><svg width="10" height="10"><use href="#note"/></svg>Www.melodybin.pk</li>
    </ul>

    <div class="more">more
      <svg width="11" height="11" viewBox="0 0 12 12"><circle cx="6" cy="6" r="6" fill="var(--pink)"/><path d="M4.8 3.4 L7.4 6 L4.8 8.6" fill="none" stroke="#fff" stroke-width="1.8"/></svg>
    </div>
  </section>

  <section class="about">
    <p class="about-lead">Velora Music is dedicated to catalog and manage audio that has been officially published online.</p>
    <p class="body">Lorem ipsum dolor sit amet, consectetur adipiscing elit, sed do eiusmod tempor incididunt ut labore et dolore magna aliqua. Ut enim ad minim veniam, quis nostrud exercitation ullamco laboris nisi ut aliquip ex ea commodo consequat. Duis aute irure dolor in reprehenderit in voluptate velit esse cillum dolore eu fugiat nulla pariatur. Excepteur sint occaecat cupidatat non proident, sunt in culpa qui officia deserunt mollit anim id est laborum.</p>
    <p class="body">Sed ut perspiciatis unde omnis iste natus error sit voluptatem accusantium doloremque laudantium, totam rem aperiam, eaque ipsa quae ab illo inventore veritatis et quasi architecto beatae vitae dicta sunt explicabo. Nemo enim ipsam voluptatem quia voluptas sit aspernatur aut odit aut fugit, sed quia consequuntur magni dolores eos qui ratione voluptatem sequi nesciunt.</p>
  </section>

  <footer class="footer">
    <div class="footer-links">DMCA<span class="sep">|</span>Terms of use<span class="sep">|</span>Privacy Policy<span class="sep">|</span>About Us<span class="sep">|</span>Recently Mp3 Added</div>
    <div class="footer-copy">All Rights Reserved. Copyrights @ 2016 company name</div>
  </footer>

</div>
</body>
</html>
```